Public Relations Agency Seeks Wordpress Design and Coding

TRELVOX Studio is a public relations agency specializing in media relations, public affairs and marketing communication.

The site should display the following visual characteristics: professionalism, trustworthiness, high-tech focus, clear and concise design.

The desired colors are royal blue, gray and hints of red.

Design look/feel inspired by this site: http://brightpathgatherings.example/

Specifications:

1. Navigation/Pages/Index:

HOME

ABOUT US

SERVICES

NEWS

CONTACT

---

2. Functionality of/content for each page:

- Home
o Dominant photo (professional, edgy, innovative)
o Simple, straightforward access to/from “Home” from other pages
o Includes logo (attached) and tagline "Unleash the power of communication"
o Direct link to “CONTACT”
o Links to social media accounts: Facebook, Twitter, LinkedIn

- About Us

o Company profile blurb
o President’s photo with short bio

- Services
o Public Relations
 Strategic communication
 Brand and reputation management
 Community relations
o Media Relations
 News coverage and contacts
 Media training and interview skills
 Crisis communications
o Congressional Affairs
 Public affairs
 Public policy
 Legislative strategy
o Mass Communication
 Speechwriting
 Presentation creation
 Social media
o Marketing Communications
 Business collateral material
 Promotional campaigns
 Special events and tradeshows

- News
o Blog-like page to post information and/or share news from other sites

- Contact
o Standard “Contact Us” form (Name, Email, Phone, Message)
o Direct Contact
 (407) 555-0164
 Marisol@TRELVOXstudio.example

Target Market(s)

Small to large businesses specializing in high technology, defense/military, medicine/healthcare, and wide array of professional services.

Industry/Entity Type

Marketing

Font styles to use
Serif
Sans Serif

Colors
0555a3
ec2027
edf3f7

Requirements
Must have
• -- Project reqires DESIGN - and - fully CODED.

-- Strong SEO

-- Optimized for mobile viewing

Thank you!

```html
<!DOCTYPE html>
<html lang="en">
<head>
<meta charset="utf-8">
<title>TRELVOX Studio — Public Relations</title>
<link rel="stylesheet" href="https://fonts.googleapis.com/css2?family=Oswald:wght@300;400;500&family=Mulish:wght@400;600;700&display=swap">
<style>
:root{
  --blue:#0b56b4;
  --blue-dark:#0555a3;
  --red:#c8171e;
  --topbar:#e6e6e6;
  --ink:#333;
  --text:#666;
  --card-gray:#f5f5f5;
  --line:#dedede;
  --input:#f0f0f0;
  --footer:#4a4a4a;
  --icon:#7a7a7a;
}
*{box-sizing:border-box;margin:0;padding:0}
html,body{width:1200px;height:2679px;overflow:hidden;background:#fff}
body{position:relative;font-family:"Mulish",sans-serif;color:var(--text)}
.abs{position:absolute}
.heading{font-family:"Oswald",sans-serif}

/* top bar */
.topbar{left:0;top:0;width:1200px;height:48px;background:var(--topbar)}
.topbar .tel{left:824px;top:12px;display:flex;align-items:center;gap:10px;font-family:"Oswald",sans-serif;font-weight:300;font-size:19px;color:var(--blue)}
.topbar .tel b{font-weight:300;color:var(--red)}
.topbar .social{left:1024px;top:9px;display:flex;gap:6px}
.topbar .social span{width:30px;height:30px;border-radius:50%;background:var(--blue)}

/* header */
.header{left:0;top:48px;width:1200px;height:81px;background:#fff}
.brand{left:73px;top:72px;display:flex;align-items:center;gap:8px;font-family:"Oswald",sans-serif;font-weight:500;font-size:27px;letter-spacing:1px;color:#555}
.brand i{width:10px;height:10px;background:var(--red);display:block}
.nav{right:73px;top:80px;display:flex;gap:22px;font-family:"Oswald",sans-serif;font-size:15px;color:#222}
.nav .sep{color:#333}

/* hero */
.hero{left:0;top:129px;width:1200px;height:416px;background:linear-gradient(120deg,#8a8178 0%,#5f5954 35%,#3e3b3b 60%,#6d6660 100%)}
.hero-title{left:0;top:294px;width:1200px;text-align:center;font-family:"Oswald",sans-serif;font-weight:400;font-size:64px;color:#fff;text-shadow:0 2px 6px rgba(0,0,0,.35)}
.hero-arrow{top:291px;width:71px;height:93px;background:rgba(0,0,0,.45);display:flex;align-items:center;justify-content:center}

/* section bands */
.band{left:0;width:1200px;height:152px;background:var(--blue);color:#fff;text-align:center}
.band h2{font-family:"Oswald",sans-serif;font-weight:400;font-size:42px;margin-top:40px;line-height:1}
.band svg{display:block;margin:20px auto 0}

/* about */
.portrait{left:73px;top:738px;width:332px;height:253px;background:linear-gradient(90deg,#6d7fa8 0%,#b5a99a 25%,#8f8c88 60%,#6e6b68 100%)}
.about-copy{left:434px;top:740px;width:684px;font-size:13px;line-height:21px;color:#666}
.about-copy p{margin-bottom:6px}
.btn{display:flex;align-items:center;justify-content:center;font-family:"Oswald",sans-serif;font-size:15px;color:#fff;background:var(--red)}
.read-more{left:434px;top:947px;width:134px;height:44px}

/* services */
.card{top:1229px;width:242px;height:370px;border:1px solid var(--line);background:#fff}
.card .icon{height:94px;display:flex;align-items:flex-end;justify-content:center}
.card h3{height:81px;display:flex;align-items:center;justify-content:center;text-align:center;font-family:"Oswald",sans-serif;font-weight:400;font-size:22px;line-height:30px;color:var(--red)}
.card .body{position:absolute;left:0;top:175px;width:240px;height:193px;background:var(--card-gray);text-align:center;padding:18px 22px 0}
.card .body p{font-size:12.5px;line-height:21px;color:#666}
.card .body a{display:block;margin-top:15px;font-family:"Oswald",sans-serif;font-size:14px;color:var(--red);text-decoration:none}

/* news */
.news-item{width:520px;height:88px}
.date{position:absolute;left:0;top:0;width:63px;height:88px;border:1px solid var(--line);text-align:center;background:#fff}
.date .m{font-family:"Oswald",sans-serif;font-size:17px;color:var(--blue);margin-top:4px;line-height:20px}
.date .d{font-family:"Oswald",sans-serif;font-size:26px;color:var(--red);line-height:28px}
.date .y{position:absolute;left:-1px;bottom:-1px;width:63px;height:28px;background:#444;color:#fff;font-family:"Oswald",sans-serif;font-size:17px;line-height:28px}
.news-text{position:absolute;left:91px;top:-4px;width:430px;font-size:12.5px;line-height:21px;color:#666}
.news-text a{display:block;margin-top:8px;font-family:"Oswald",sans-serif;font-size:14px;color:var(--red);text-decoration:none}

/* contact */
.address{left:73px;top:2318px;width:240px}
.address h4,.form-title{font-family:"Oswald",sans-serif;font-weight:400;font-size:20px;color:var(--blue)}
.address .company{font-family:"Oswald",sans-serif;font-size:14px;color:var(--red);letter-spacing:.5px;margin:8px 0 12px}
.address p{font-size:12.5px;line-height:20px;color:#555}
.address b{color:var(--red);font-weight:600}
.form-title{left:343px;top:2318px}
.label{font-family:"Oswald",sans-serif;font-size:14px;color:var(--red)}
.field{background:var(--input);border:1px solid #d4d4d4}
.submit{left:1002px;top:2513px;width:125px;height:45px;background:var(--blue)}

/* footer */
.footer{left:0;top:2593px;width:1200px;height:86px;background:var(--footer);text-align:center;color:#bdbdbd;font-size:10.5px;line-height:18px;letter-spacing:.5px;padding-top:24px}
</style>
</head>
<body>

<div class="abs topbar"></div>
<div class="abs topbar tel" style="background:none;width:auto;height:auto">
  <svg width="18" height="18" viewBox="0 0 18 18"><rect width="18" height="18" rx="2" fill="#555"/><path d="M5 4c1 0 1.5 2 1.5 2.5S5.5 7.5 5.8 8.3c.5 1.4 2.4 3.3 3.8 3.8.8.3 1.3-.8 1.8-.8s2.5.6 2.5 1.5c0 1-1.2 1.7-2 1.7C8 14.5 3.5 10 3.5 6 3.5 5 4.2 4 5 4z" fill="#fff"/></svg>
  <span><b>Tel:</b> 123-456-7890</span>
</div>
<div class="abs social" style="left:1024px;top:9px;display:flex;gap:6px">
  <span style="width:30px;height:30px;border-radius:50%;background:#3b5998"></span>
  <span style="width:30px;height:30px;border-radius:50%;background:#3b8fd6"></span>
  <span style="width:30px;height:30px;border-radius:50%;background:#1e6fb5"></span>
</div>

<header class="abs header"></header>
<div class="abs brand"><span>TRELVOX Studio</span><i></i></div>
<nav class="abs nav">
  <span>HOME</span><span class="sep">&gt;&gt;</span>
  <span>ABOUT US</span><span class="sep">&gt;&gt;</span>
  <span>SERVICES</span><span class="sep">&gt;&gt;</span>
  <span>NEWS</span><span class="sep">&gt;&gt;</span>
  <span>CONTACT US</span>
</nav>

<section class="abs hero" role="img" aria-label="Photo of business professionals networking and talking at an event"></section>
<h1 class="abs hero-title">Unleash the Power of Communication</h1>
<div class="abs hero-arrow" style="left:0"><svg width="16" height="26" viewBox="0 0 16 26"><path d="M14 2 3 13l11 11" fill="none" stroke="#fff" stroke-width="2"/></svg></div>
<div class="abs hero-arrow" style="right:0"><svg width="16" height="26" viewBox="0 0 16 26"><path d="M2 2l11 11L2 24" fill="none" stroke="#fff" stroke-width="2"/></svg></div>

<!-- About -->
<section class="abs band" style="top:545px"><h2>ABOUT US</h2><svg width="22" height="12" viewBox="0 0 22 12"><path d="M1 1l10 9 10-9" fill="none" stroke="#fff" stroke-width="2"/></svg></section>
<div class="abs portrait" role="img" aria-label="Portrait photo of the agency president in front of a flag"></div>
<div class="abs about-copy">
  <p>Aliquam molestie, mi et imperdiet euismod, dui purus auctor tellus, et interdum lacus lectus et ante. Sed accumsan sollicitudin sapien, sit amet adipiscing turpis gravida ac. In congue, neque ac lobortis volutpat, libero mauris varius mi, vitae suscipit ipsum ligula vitae risus. Duis aliquam nibh a dui iaculis viverra id a velit. Vivamus egestas risus in magna varius commodo. Sed semper viverra egestas.</p>
  <p>Vestibulum dolor nulla, ultrices ac tincidunt sed, laoreet non est. Suspendisse lobortis turpis in odio blandit ac interdum lorem euismod. Etiam risus massa, vulputate eu pellentesque et, consectetur a neque.</p>
  <p>Nunc consequat congue nulla eu imperdiet. Donec in est erat, id malesuada turpis. Nunc a dui id turpis convallis semper. Nunc dignissim lectus vitae eros placerat euismod.</p>
</div>
<a class="abs btn read-more">READ MORE &gt;&gt;</a>

<!-- Services -->
<section class="abs band" style="top:1034px"><h2>OUR SERVICES</h2><svg width="22" height="12" viewBox="0 0 22 12"><path d="M1 1l10 9 10-9" fill="none" stroke="#fff" stroke-width="2"/></svg></section>

<div class="abs card" style="left:73px">
  <div class="icon"><svg width="96" height="72" viewBox="0 0 96 72" fill="var(--icon)"><path d="M2 2h54v34H24L12 46V36H2z"/><path d="M40 24h54v34H84v10L72 58H40z" stroke="#fff" stroke-width="3"/></svg></div>
  <h3>PUBLIC RELATIONS</h3>
  <div class="body"><p>Duis aliquam nibh a dui iaculis viverra id a velit. Vivamus egestas risus in magna varius commodo. Sed semper viverra egestas. Suspendisse lobortis turpis in odio blandit ac interdum..</p><a>LEARN MORE &gt;&gt;</a></div>
</div>
<div class="abs card" style="left:345px">
  <div class="icon"><svg width="56" height="76" viewBox="0 0 56 76" fill="none" stroke="var(--icon)" stroke-width="4"><rect x="16" y="2" width="24" height="42" rx="12" fill="var(--icon)"/><path d="M6 30c0 14 10 24 22 24s22-10 22-24M28 54v16M14 72h28"/></svg></div>
  <h3>MEDIA RELATIONS</h3>
  <div class="body"><p>Duis aliquam nibh a dui iaculis viverra id a velit. Vivamus egestas risus in magna varius commodo. Sed semper viverra egestas. Suspendisse lobortis turpis in odio blandit ac interdum..</p><a>LEARN MORE &gt;&gt;</a></div>
</div>
<div class="abs card" style="left:614px">
  <div class="icon"><svg width="72" height="72" viewBox="0 0 72 72" fill="var(--icon)"><circle cx="36" cy="36" r="22" fill="none" stroke="var(--icon)" stroke-width="2" stroke-dasharray="4 4"/><circle cx="36" cy="8" r="6"/><circle cx="36" cy="64" r="6"/><circle cx="8" cy="36" r="6"/><circle cx="64" cy="36" r="6"/><circle cx="16" cy="16" r="5"/><circle cx="56" cy="16" r="5"/><circle cx="16" cy="56" r="5"/><circle cx="56" cy="56" r="5"/><circle cx="36" cy="32" r="6"/><path d="M26 46c0-6 4-9 10-9s10 3 10 9z"/></svg></div>
  <h3>PUBLIC AFFAIRS</h3>
  <div class="body"><p>Duis aliquam nibh a dui iaculis viverra id a velit. Vivamus egestas risus in magna varius commodo. Sed semper viverra egestas. Suspendisse lobortis turpis in odio blandit ac interdum..</p><a>LEARN MORE &gt;&gt;</a></div>
</div>
<div class="abs card" style="left:884px">
  <div class="icon"><svg width="84" height="72" viewBox="0 0 84 72" fill="var(--icon)"><path d="M6 40l46-30 12 34-50 8z"/><rect x="2" y="40" width="12" height="14" rx="2" transform="rotate(-12 8 47)"/><path d="M20 52l6 16h8l-4-17z"/><path d="M66 18c4 2 6 6 6 10M70 10c6 3 10 10 10 18" fill="none" stroke="var(--icon)" stroke-width="3"/></svg></div>
  <h3>MARKETING<br>COMMUNICATION</h3>
  <div class="body"><p>Duis aliquam nibh a dui iaculis viverra id a velit. Vivamus egestas risus in magna varius commodo. Sed semper viverra egestas. Suspendisse lobortis turpis in odio blandit ac interdum..</p><a>LEARN MORE &gt;&gt;</a></div>
</div>

<!-- News -->
<section class="abs band" style="top:1649px"><h2>LATEST NEWS</h2><svg width="22" height="12" viewBox="0 0 22 12"><path d="M1 1l10 9 10-9" fill="none" stroke="#fff" stroke-width="2"/></svg></section>

<article class="abs news-item" style="left:73px;top:1847px"><div class="date"><div class="m">Sep</div><div class="d">29</div><div class="y">2014</div></div><div class="news-text">Duis aliquam nibh a dui iaculis viverra id a velit. Vivamus egestas risus in magna varius commodo. Sed semper viverra egestas. Suspendisse lobortis turpis in odio blandit ac interdum..<a>LEARN MORE &gt;&gt;</a></div></article>
<article class="abs news-item" style="left:613px;top:1847px"><div class="date"><div class="m">Sep</div><div class="d">29</div><div class="y">2014</div></div><div class="news-text">Duis aliquam nibh a dui iaculis viverra id a velit. Vivamus egestas risus in magna varius commodo. Sed semper viverra egestas. Suspendisse lobortis turpis in odio blandit ac interdum..<a>LEARN MORE &gt;&gt;</a></div></article>
<article class="abs news-item" style="left:73px;top:1979px"><div class="date"><div class="m">Sep</div><div class="d">29</div><div class="y">2014</div></div><div class="news-text">Duis aliquam nibh a dui iaculis viverra id a velit. Vivamus egestas risus in magna varius commodo. Sed semper viverra egestas. Suspendisse lobortis turpis in odio blandit ac interdum..<a>LEARN MORE &gt;&gt;</a></div></article>
<article class="abs news-item" style="left:613px;top:1979px"><div class="date"><div class="m">Sep</div><div class="d">29</div><div class="y">2014</div></div><div class="news-text">Duis aliquam nibh a dui iaculis viverra id a velit. Vivamus egestas risus in magna varius commodo. Sed semper viverra egestas. Suspendisse lobortis turpis in odio blandit ac interdum..<a>LEARN MORE &gt;&gt;</a></div></article>

<!-- Contact -->
<section class="abs band" style="top:2125px"><h2>CONTACT US</h2><svg width="22" height="12" viewBox="0 0 22 12"><path d="M1 1l10 9 10-9" fill="none" stroke="#fff" stroke-width="2"/></svg></section>

<div class="abs address">
  <h4>ADDRESS:</h4>
  <div class="company">COMPANY NAME</div>
  <p>4120 Larkfield<br>Lane,Dunmore, D07 41KT.</p>
  <p style="margin-top:10px"><b>Ph:</b> 123-456-7890<br><b>Email:</b> info@trelvoxstudio.example</p>
</div>

<div class="abs form-title">CONTACT FORM</div>
<div class="abs label" style="left:343px;top:2355px">NAME</div>
<div class="abs field" style="left:343px;top:2376px;width:361px;height:37px"></div>
<div class="abs label" style="left:343px;top:2428px">CONTACT NO.</div>
<div class="abs field" style="left:343px;top:2449px;width:361px;height:37px"></div>
<div class="abs label" style="left:343px;top:2500px">EMAIL ADDRESS.</div>
<div class="abs field" style="left:343px;top:2522px;width:361px;height:36px"></div>
<div class="abs label" style="left:764px;top:2355px">COMMENTS</div>
<div class="abs field" style="left:764px;top:2376px;width:363px;height:110px"></div>
<a class="abs btn submit">SUBMIT NOW</a>

<footer class="abs footer">COPYRIGHT © 2014, COMPANY NAME.<br>ALL RIGHT RESERVED</footer>

</body>
</html>
```